QVR business card

Need a business card for a company that provides instructional design and elearning development services. The website is here: http://quorvane.studio/

I'm attaching a current logo, as well as the old business card design. While I like to keep it clean, the old design is too simplistic for my liking. The only idea I want to reuse from the old design is placing industry jargon on the back of the card, just need a better way to present it. But if you have other ideas for the back--feel free to experiment.

Please use the colors complementary to the color we have on the website. Thank you!

```html
<!DOCTYPE html>
<html lang="en">
<head>
<meta charset="utf-8">
<title>QVR business card</title>
<link rel="stylesheet" href="https://fonts.googleapis.com/css2?family=Nunito:wght@700;800&family=Roboto:wght@400&display=swap">
<style>
  :root {
    --backdrop: #a4a2a2;
    --card: #2f2f30;
    --gold: #d8d38a;
    --teal: #2db3a4;
    --teal-light: #9fd09a;
    --grey-text: #a9a9ab;
    --contact: #c2c2c4;
    --white: #ffffff;
  }
  * { margin: 0; padding: 0; box-sizing: border-box; }
  html, body { width: 1200px; height: 1200px; overflow: hidden; }
  body { background: var(--backdrop); position: relative; font-family: "Nunito", sans-serif; }

  .card {
    position: absolute;
    width: 712px;
    height: 418px;
    border-radius: 28px;
    background: var(--card);
    overflow: hidden;
  }
  .card--front { left: 238px; top: 118px; }
  .card--back { left: 231px; top: 643px; }

  /* Front */
  .headline { position: absolute; inset: 0; font-weight: 800; line-height: 1; }
  .headline span { position: absolute; white-space: nowrap; }
  .headline__how { left: 250px; top: 102px; font-size: 76px; color: var(--gold); }
  .headline__can { left: 188px; top: 160px; font-size: 76px; color: var(--grey-text); }
  .headline__we { left: 352px; top: 176px; font-size: 50px; color: var(--teal); }
  .headline__help { left: 247px; top: 233px; font-size: 76px; color: var(--gold); }
  .headline__mark { left: 454px; top: 138px; font-size: 190px; color: var(--teal); }

  /* Back */
  .wave { position: absolute; inset: 0; width: 712px; height: 418px; }
  .holder-name {
    position: absolute; right: 36px; top: 40px;
    text-align: center; color: var(--white);
    font-weight: 800; font-size: 24px; line-height: 32px;
  }
  .brand {
    position: absolute; left: 52px; top: 160px;
    display: flex; align-items: center; gap: 16px;
  }
  .brand__square { width: 34px; height: 34px; background: var(--teal); border-radius: 4px; }
  .brand__name { color: var(--gold); font-weight: 800; font-size: 44px; line-height: 1; }

  .contacts {
    position: absolute; left: 52px; top: 292px;
    list-style: none; font-family: "Roboto", sans-serif;
    font-size: 18px; color: var(--contact);
  }
  .contacts li { display: flex; align-items: center; height: 27.5px; }
  .contacts svg { width: 16px; height: 16px; margin-right: 18px; fill: var(--teal); }
</style>
</head>
<body>

<section class="card card--front" aria-label="Card front">
  <h1 class="headline">
    <span class="headline__how">How</span>
    <span class="headline__can">can</span>
    <span class="headline__we">we</span>
    <span class="headline__help">Help</span>
    <span class="headline__mark">?</span>
  </h1>
</section>

<section class="card card--back" aria-label="Card back">
  <svg class="wave" viewBox="0 0 712 418" aria-hidden="true">
    <defs>
      <linearGradient id="bandFill" x1="0" y1="0" x2="0" y2="1">
        <stop offset="0" stop-color="var(--teal-light)"/>
        <stop offset="0.45" stop-color="var(--teal)"/>
        <stop offset="1" stop-color="#3cb3aa"/>
      </linearGradient>
    </defs>
    <path d="M0 0 H712 V182 C640 170 580 150 500 110 C400 60 300 40 150 42 C90 42 40 44 0 48 Z" fill="url(#bandFill)"/>
    <path d="M0 40 C120 14 260 10 360 36 C300 26 200 24 110 36 C60 42 20 48 0 56 Z" fill="var(--card)"/>
    <path d="M0 48 C40 44 90 42 150 42 C300 40 400 60 500 110 C580 150 640 170 712 182 V190 C640 178 580 160 500 118 C400 68 300 48 150 50 C90 50 40 52 0 56 Z" fill="var(--card)"/>
    <path d="M60 62 C200 42 340 50 450 100 C560 150 630 180 712 188" fill="none" stroke="var(--gold)" stroke-width="5"/>
  </svg>

  <div class="holder-name">Maren<br>Talvik</div>

  <div class="brand">
    <div class="brand__square"></div>
    <div class="brand__name">Quorvane Studio</div>
  </div>

  <ul class="contacts">
    <li>
      <svg viewBox="0 0 16 16"><path d="M1 6c0-3 3-4 7-4s7 1 7 4v1h-4V5H5v2H1zM4 8h8l2 6H2z"/></svg>
      555-013-2748
    </li>
    <li>
      <svg viewBox="0 0 16 16"><path d="M8 1a7 7 0 1 0 0 14A7 7 0 0 0 8 1zm0 1.6c.8 0 1.7 1.6 2 4.2H6c.3-2.6 1.2-4.2 2-4.2zM2.7 6.8a5.4 5.4 0 0 1 2.2-3.3c-.4 1-.7 2.1-.8 3.3zm0 2.4h1.4c.1 1.2.4 2.3.8 3.3a5.4 5.4 0 0 1-2.2-3.3zM8 13.4c-.8 0-1.7-1.6-2-4.2h4c-.3 2.6-1.2 4.2-2 4.2zm3.1-.9c.4-1 .7-2.1.8-3.3h1.4a5.4 5.4 0 0 1-2.2 3.3zm.8-5.7c-.1-1.2-.4-2.3-.8-3.3a5.4 5.4 0 0 1 2.2 3.3z"/></svg>
      www.quorvane.studio
    </li>
    <li>
      <svg viewBox="0 0 16 16"><path d="M1 3h14v10H1zM2.5 4.5 8 9l5.5-4.5V11.5h-11z" fill-rule="evenodd"/></svg>
      mtalvik@quorvane.studio
    </li>
  </ul>
</section>

</body>
</html>
```